Satchel & Sundial needs new business card design

I need a new business card design. I'm looking for out-of-the-box design which represents the freedom of being a location independent entrepreneur.
I offer coaching, retreats and trips.
I would like to see designs with and without the photo.
Colors I use are black (#000000), green (#25A796) and brown (#D7C38C)
Website satchelandsundial.example

Target Market(s)

location independent entrepreneurs, digital nomads, people looking to swap the 9 to 5 for a lifestyle business

Industry/Entity Type

Business

Contact Information for Business Card

Dorota Falkner
Your Lifestyle Business Coach, Retreat & Trip Leader
http://satchelandsundial.example
hello@satchelandsundial.example
Live a life you don't need a holiday from

Font styles to use
Serif
Sans Serif

Requirements
Must have
• One side should contain only the logo. I would also consider having the "Live a life you don't need a holiday from" on that side too (depending on how it looks)
• Please show both sides on the designs.

```html
<!DOCTYPE html>
<html lang="en">
<head>
<meta charset="utf-8">
<title>Satchel &amp; Sundial — Business Card</title>
<link href="https://fonts.googleapis.com/css2?family=Oswald:wght@300;400;500&display=swap" rel="stylesheet">
<style>
  :root {
    --backdrop: #e4e4e4;
    --green: #25a796;
    --green-deep: #008b7e;
    --green-top: #009688;
    --ink: #1f2124;
    --gold: #d7c38c;
    --white: #ffffff;
    --soft-white: #e9ecec;
    --photo-light: #a9b59a;
    --photo-dark: #55683f;
  }
  * { margin: 0; padding: 0; box-sizing: border-box; }
  html, body {
    width: 1200px; height: 576px; overflow: hidden;
    background: var(--backdrop);
    font-family: "Oswald", "Arial Narrow", sans-serif;
  }
  .stage { position: relative; width: 1200px; height: 576px; }
  .card {
    position: absolute; width: 484px; height: 292px;
    border-radius: 6px; overflow: hidden;
  }
  /* Front */
  .card-front {
    left: 82px; top: 139px;
    background: linear-gradient(180deg, var(--green-top), var(--green-deep));
    color: var(--white); text-align: center;
  }
  .brand-name {
    position: absolute; left: 0; right: 0; top: 92px;
    font-weight: 400; font-size: 38px; letter-spacing: 1px;
    text-transform: uppercase; line-height: 1;
  }
  .front-web {
    position: absolute; left: 0; right: 0; top: 184px;
    font-weight: 400; font-size: 12px; letter-spacing: 2.2px;
  }
  /* Back */
  .card-back { left: 602px; top: 138px; width: 481px; height: 291px; background: var(--ink); }
  .card-back svg.portrait { position: absolute; left: 0; top: 0; }
  .person-name {
    position: absolute; left: 28px; top: 34px;
    color: var(--gold); font-weight: 500; font-size: 19px;
    text-transform: uppercase; letter-spacing: 0.3px; line-height: 1;
  }
  .person-role {
    position: absolute; left: 28px; top: 60px;
    color: var(--white); font-weight: 300; font-size: 10.5px; line-height: 1.45;
  }
  .contact-list { position: absolute; left: 28px; top: 154px; list-style: none; }
  .contact-list li {
    display: flex; align-items: center; height: 21px;
    color: var(--soft-white); font-weight: 300; font-size: 11.5px;
  }
  .contact-list svg { width: 11px; height: 11px; margin-right: 9px; flex: none; }
  .tagline {
    position: absolute; left: 28px; top: 238px;
    color: var(--green); font-weight: 400; font-size: 12.5px;
  }
</style>
</head>
<body>
<main class="stage">
  <section class="card card-front">
    <h1 class="brand-name">Satchel &amp; Sundial</h1>
    <p class="front-web">www.satchelandsundial.example</p>
  </section>

  <section class="card card-back">
    <svg class="portrait" width="481" height="291" viewBox="0 0 481 291">
      <defs>
        <linearGradient id="foliage" x1="0" y1="0" x2="1" y2="1">
          <stop offset="0" stop-color="var(--photo-light)"/>
          <stop offset="1" stop-color="var(--photo-dark)"/>
        </linearGradient>
        <linearGradient id="arc-fade" x1="0" y1="0" x2="0" y2="1">
          <stop offset="0" stop-color="var(--green)"/>
          <stop offset="1" stop-color="var(--green)" stop-opacity="0"/>
        </linearGradient>
      </defs>
      <path role="img" aria-label="Photo of the coach sitting on a garden fence under trees, holding a small sign"
            d="M294 0 Q246 145 270 291 L481 291 L481 0 Z" fill="url(#foliage)"/>
      <path d="M292 0 L314 0 Q262 62 253 175 Q246 72 292 0 Z" fill="url(#arc-fade)"/>
    </svg>

    <h2 class="person-name">Dorota Falkner</h2>
    <p class="person-role">Your Lifestyle Business Coach,<br>Retreat Facilitator and Trip Leader</p>

    <ul class="contact-list">
      <li>
        <svg viewBox="0 0 11 11"><rect x="0.5" y="2" width="10" height="7" fill="var(--green)"/><path d="M0.5 2 L5.5 6 L10.5 2" stroke="var(--ink)" stroke-width="1" fill="none"/></svg>
        hello@satchelandsundial.example
      </li>
      <li>
        <svg viewBox="0 0 11 11"><circle cx="5.5" cy="5.5" r="4.8" fill="none" stroke="var(--green)" stroke-width="1.1"/><ellipse cx="5.5" cy="5.5" rx="2" ry="4.8" fill="none" stroke="var(--green)" stroke-width="0.9"/><path d="M0.7 5.5 H10.3" stroke="var(--green)" stroke-width="0.9"/></svg>
        www.satchelandsundial.example
      </li>
      <li>
        <svg viewBox="0 0 11 11"><rect x="0.5" y="0.5" width="10" height="10" rx="1.5" fill="var(--green)"/></svg>
        /satchelandsundial
      </li>
    </ul>

    <p class="tagline">Live a life you don’t need a holiday from</p>
  </section>
</main>
</body>
</html>
```